Book cover design for a collection of poetry - The Lanternfield

Book cover and back design need to be moody, nostalgic, reflective, ethereal. Melancholy and other worldly. Cover design should not be time specific to a period or place but if applicable should reflect British landscape. Book cover should be in tones of blue and must include the title and author (THE LANTERNFIELD BY CORBIN WHITLACE). We love the idea of rain, and looking out of a window. See attached designs. A world you are observing but not in.

Industry/Entity Type

Book Publisher

Font styles to use
Serif
Script

Colors
3176b5
3377b5
85acd3
eaf1f7
0792cd
33a6d7
86cae7
ecf7fb
86cfc6

Requirements
Must have
• The colour blue in it, must be melancholy and reflective.
Nice to have
• Rain in the cover.
Should not have
• Any bright colours.

```html
<!DOCTYPE html>
<html lang="en">
<head>
<meta charset="utf-8">
<title>The Lanternfield — Corbin Whitlace — Full Cover</title>
<link rel="stylesheet" href="https://fonts.googleapis.com/css2?family=EB+Garamond:wght@400;500;600;700&display=swap">
<style>
  :root {
    --night: #040812;
    --deep-teal: #17403f;
    --sea-teal: #22504c;
    --slate-title-dark: #3e5566;
    --spine-title: #90a6b4;
    --pale-ink: #eef2f3;
    --curtain: #b9bdc0;
    --curtain-shade: #7c8186;
    --frame-grey: #5d6266;
    --garden-green: #6f7a66;
    --paper: #ffffff;
    --ink: #111111;
  }
  html, body {
    margin: 0;
    padding: 0;
    width: 1200px;
    height: 914px;
    overflow: hidden;
    background: var(--night);
  }
  .cover {
    position: relative;
    width: 1200px;
    height: 914px;
    overflow: hidden;
    font-family: "EB Garamond", Georgia, serif;
  }
  .rain-glass {
    position: absolute;
    inset: 0;
    background:
      radial-gradient(ellipse 420px 360px at 300px 420px, rgba(34, 88, 82, 0.75), transparent 70%),
      radial-gradient(ellipse 300px 500px at 650px 300px, rgba(23, 64, 63, 0.7), transparent 75%),
      linear-gradient(180deg, var(--deep-teal) 0%, #0c2228 45%, var(--night) 100%);
  }
  .window-view {
    position: absolute;
    top: 0;
    left: 700px;
    width: 500px;
    height: 914px;
    background:
      linear-gradient(180deg, rgba(10, 26, 30, 0.95) 0%, rgba(10, 26, 30, 0.85) 14%, rgba(10, 26, 30, 0) 22%),
      linear-gradient(90deg,
        rgba(4, 10, 18, 0) 0%,
        rgba(40, 52, 58, 0.6) 8%,
        var(--curtain-shade) 16%,
        var(--curtain) 26%,
        #d3d6d8 33%,
        var(--curtain-shade) 42%,
        var(--frame-grey) 46%,
        #8e9188 50%,
        #a58a86 55%,
        var(--garden-green) 64%,
        #8a9184 78%,
        var(--frame-grey) 84%,
        #7f8678 90%,
        #6a7262 100%);
  }
  .headings {
    position: absolute;
    inset: 0;
  }
  .blurb {
    position: absolute;
    left: 40px;
    top: 176px;
    width: 492px;
    margin: 0;
    color: var(--pale-ink);
    font-size: 20.5px;
    line-height: 28.6px;
    text-align: center;
  }
  .blurb p {
    margin: 0 0 28.6px;
  }
  .barcode-box {
    position: absolute;
    left: 171px;
    top: 720px;
    width: 229px;
    height: 137px;
    background: var(--paper);
    color: var(--ink);
    font-size: 16px;
    display: flex;
    align-items: center;
    justify-content: center;
    padding-top: 12px;
    box-sizing: border-box;
  }
</style>
</head>
<body>
<main class="cover">
  <div class="rain-glass" role="img" aria-label="Photograph of rain running down dark blue-green window glass"></div>
  <div class="window-view" role="img" aria-label="Photograph of a pale curtain beside a rain-streaked window, looking out onto a red telephone box, long grass and a stone wall"></div>

  <svg class="headings" width="1200" height="914" viewBox="0 0 1200 914" xmlns="http://www.w3.org/2000/svg">
    <defs>
      <filter id="emboss-shadow" x="-10%" y="-10%" width="120%" height="130%">
        <feDropShadow dx="2" dy="2" stdDeviation="1.5" flood-color="#000" flood-opacity="0.85"/>
      </filter>
      <linearGradient id="title-metal" x1="0" y1="0" x2="0" y2="1">
        <stop offset="0" stop-color="#8aa3b3"/>
        <stop offset="1" stop-color="#4f6778"/>
      </linearGradient>
      <linearGradient id="title-metal-vertical" x1="1" y1="0" x2="0" y2="0">
        <stop offset="0" stop-color="#8aa3b3"/>
        <stop offset="1" stop-color="#4f6778"/>
      </linearGradient>
    </defs>

    <text class="back-title" x="60" y="98" font-family="EB Garamond, Georgia, serif" font-weight="700" font-size="58" fill="url(#title-metal)" stroke="var(--slate-title-dark)" stroke-width="0.8" textLength="454" lengthAdjust="spacingAndGlyphs" filter="url(#emboss-shadow)">THE LANTERNFIELD</text>

    <text class="spine-title" transform="translate(590 60) rotate(90)" font-family="EB Garamond, Georgia, serif" font-weight="500" font-size="38" fill="var(--spine-title)" textLength="313" lengthAdjust="spacingAndGlyphs" filter="url(#emboss-shadow)">THE LANTERNFIELD</text>

    <text class="spine-author" transform="translate(590 471) rotate(90)" font-family="EB Garamond, Georgia, serif" font-weight="500" font-size="38" fill="var(--pale-ink)" textLength="389" lengthAdjust="spacingAndGlyphs" filter="url(#emboss-shadow)">CORBIN WHITLACE</text>

    <text class="front-title" transform="translate(696 60) rotate(90)" font-family="EB Garamond, Georgia, serif" font-weight="500" font-size="112" fill="url(#title-metal-vertical)" stroke="var(--slate-title-dark)" stroke-width="1" textLength="800" lengthAdjust="spacingAndGlyphs" filter="url(#emboss-shadow)">THE LANTERNFIELD</text>

    <text class="front-author" transform="translate(786 57) rotate(90)" font-family="EB Garamond, Georgia, serif" font-weight="500" font-size="46" fill="var(--pale-ink)" textLength="308" lengthAdjust="spacingAndGlyphs" filter="url(#emboss-shadow)">Corbin Whitlace</text>
  </svg>

  <section class="blurb">
    <p>The Lanternfield is a collection of poetry.</p>
    <p>Told in two parts we first meet Charles - aged, crippled<br>
    and left alone in his inherites marsh house - reflecting<br>
    on his life and his marriage to beautiful Alice who we<br>
    meet inpart two. Alice is suicidal, manically depressed<br>
    and struggling with life as a wife and mother. She meets,<br>
    harbors and falls in love with a soldier during wwii and<br>
    her world is changed forever.</p>
    <p>Moving through the 20th century, this life and the next,<br>
    The Lanternfield interweaves grief, loss, the after-life,<br>
    mental illness, and ultimately the true nature of love.</p>
  </section>

  <div class="barcode-box">BARCODE</div>
</main>
</body>
</html>
```